Harvest Gateway Fellowship Ministries needs a fresh new web design

We are an up and coming multicultural church that aims to bring people into a life changing encounter with God. We need a fresh and inviting website in order to increase our internet presence and make us easier to connect with.
Here are some of the basic requirements for the site:
• Clearly displayed address, service times, and contact info
• A staff profile page
• An area for a calendar with upcoming events and their details
• Social media buttons
• Group pages for the different ministries (youth, children’s church, men, etc…)
• An area for donations and eCommerce
• A resources page for assorted media (podcasts, sermons, videos, etc.…)
• An area for prayer requests.

```html
<!DOCTYPE html>
<html lang="en">
<head>
<meta charset="utf-8">
<title>Harvest Gateway Fellowship Ministries</title>
<link href="https://fonts.googleapis.com/css2?family=Open+Sans:ital,wght@0,400;0,600;1,400&display=swap" rel="stylesheet">
<style>
:root{--navy:#0b4a7a;--navy-dark:#083a5e;--gold:#efbc3b;--cell:#dedede;--ink:#222;--muted:#666;--line:#cfcfcf}
*{box-sizing:border-box;margin:0;padding:0}
html,body{width:758px;height:1200px;overflow:hidden;background:#fff;font-family:"Open Sans",sans-serif;color:var(--ink)}
.page{position:relative;width:758px;height:1200px}
.abs{position:absolute}
.brand{left:76px;top:30px;display:flex;align-items:center;gap:8px;width:200px}
.brand-mark{width:38px;height:38px;border-radius:50%;background:var(--gold);flex:none}
.brand-name{font-size:11px;font-weight:600;color:var(--navy);line-height:1.3}
.daily{left:518px;top:26px;width:158px;height:74px;background:var(--gold);border:1px solid #d9a520;padding:6px 10px;font-size:7px;line-height:1.75}
.daily h3{font-size:9px;font-weight:400;color:var(--navy);margin-bottom:6px}
.daily p{text-align:justify;color:#333}
.daily .ref{font-weight:600}
.nav{left:82px;width:594px;height:30px;background:var(--navy);display:flex;align-items:center;justify-content:space-around;padding:0 4px}
.nav a{color:#fff;font-size:8px;font-weight:600;text-decoration:none;padding:8px 14px}
.nav a.on{background:var(--gold);color:#222;padding:9px 24px}
.top-nav{top:116px}
.hero{left:82px;top:146px;width:594px;height:226px;background:linear-gradient(90deg,#b79a78 0%,#d8d2c6 40%,#eceae6 62%,#c98c7c 75%,#e4dbd4 100%)}
.hero-arrow{right:8px;top:98px;color:#8fb0cc;font-size:26px}
.dots{left:280px;top:359px;display:flex;gap:2px}
.dots span{width:8px;height:8px;border-radius:50%;border:1px solid #6f8fa8}
.dots span.on{background:#5b86a8}
h2{font-weight:400;color:var(--navy)}
.welcome{left:83px;top:406px;width:368px;font-size:6.6px;line-height:1.95}
.welcome h2{font-size:13px;margin-bottom:8px}
.welcome p{margin-bottom:10px}
.welcome .hope{font-size:9px;color:var(--navy)}
.visit{left:495px;top:410px;width:181px;height:138px;border:1px solid var(--line);background:#f7f7f7;padding:8px 17px;font-size:7px;line-height:1.9}
.visit h2{font-size:12px;margin-bottom:2px}
.visit h4{font-size:9px;font-weight:400;color:var(--navy);margin-top:6px}
.visit .org{font-size:9px}
.prayer{left:82px;top:582px;width:370px;height:138px;border:1px solid var(--line)}
.prayer h2{position:absolute;left:8px;top:10px;font-size:12px}
.search{position:absolute;left:270px;top:14px;width:72px;height:14px;background:#eee;font-size:6.5px;color:#666;padding:2px 6px}
.req-title{position:absolute;left:11px;top:42px;font-size:9px;color:var(--navy)}
.req-row{position:absolute;left:0;top:56px;width:368px;height:22px;background:#f3f3f3;font-size:6.5px;font-style:italic;padding:6px 8px;display:flex;gap:16px}
.req-row b{font-style:normal;font-weight:400;color:#000;font-size:8px;margin-top:-1px}
.req-meta{position:absolute;left:8px;top:84px;width:352px;font-size:6.5px;color:var(--muted);display:flex;justify-content:space-between;border-bottom:1px solid #e5e5e5;padding-bottom:6px}
.pager{position:absolute;left:8px;top:110px;color:#8fb0cc;font-size:12px}
.sort{position:absolute;left:270px;top:110px;width:72px;height:14px;background:#eee;font-size:6.5px;color:#555;padding:2px 6px}
.donate{left:495px;top:582px;width:181px;height:73px;background:var(--navy);color:#fff;padding:10px 16px;font-size:7px;line-height:1.8}
.donate h2{color:#fff;font-size:14px;margin-bottom:4px}
.donate small{font-size:6px;font-style:italic;margin:0 3px 0 6px}
.donate .pay{font-size:13px;font-weight:600;color:#9cc8ec}
.shop{left:495px;top:655px;width:181px;height:65px;background:var(--gold);color:var(--navy);padding:6px 16px;font-size:7px;line-height:1.8}
.shop h2{font-size:12px;margin-bottom:6px}
.cart{position:absolute;right:20px;top:8px}
.cal-title{left:82px;top:751px;font-size:12.5px}
.cal-month{right:82px;top:751px;font-size:12.5px;color:#111}
.cal-month span{color:#8fb0cc}
.cal{left:82px;top:774px;width:594px;height:264px;display:grid;grid-template-columns:repeat(7,1fr);grid-template-rows:repeat(6,1fr);gap:2px}
.cal div{background:var(--cell);display:flex;flex-direction:column;align-items:center;justify-content:center;font-size:13px;color:#333}
.cal div.ev{background:var(--gold);color:#fff}
.cal div.ev small{font-size:6.5px}
.quote{left:0;width:758px;top:1064px;text-align:center;color:var(--navy);font-size:12px}
.foot-nav{top:1100px;height:36px}
.footer{left:82px;top:1136px;width:594px;height:64px;background:var(--navy-dark);color:#fff}
.foot-links{position:absolute;left:12px;top:8px;font-size:8px;line-height:1.9}
.follow{position:absolute;left:224px;top:8px;font-size:8px;text-align:center}
.social{display:flex;gap:3px;margin-top:6px;justify-content:center}
.social span{width:20px;height:20px;border-radius:50%;border:1.5px solid #fff}
.legal{position:absolute;right:12px;top:30px;font-size:6.5px;line-height:1.6}
</style>
</head>
<body>
<div class="page">
  <div class="abs brand"><span class="brand-mark"></span><span class="brand-name">Harvest Gateway Fellowship Ministries</span></div>
  <aside class="abs daily">
    <h3>Daily Bread !</h3>
    <p>Let not your heart be troubled: ye believe in God, believe also in me.</p>
    <p class="ref">John 14:1</p>
  </aside>
  <nav class="abs nav top-nav">
    <a class="on">Home</a><a>About Us</a><a>Events</a><a>Prayer Request</a><a>Resources</a><a>Donate</a><a>Contact Us</a>
  </nav>
  <div class="abs hero" role="img" aria-label="Sanctuary with pulpit and drum kit beside a portrait of a church member">
    <span class="abs hero-arrow">&#x27E9;</span>
  </div>
  <div class="abs dots"><span></span><span></span><span></span><span class="on"></span></div>

  <section class="abs welcome">
    <h2>Welcome to HGFM</h2>
    <p>Welcome to Harvest Gateway Fellowship Ministries, a place where we can come together and fellowship. HGFM is located in Riverside, New York and we would love to have you worship with us. We believe God is doing something extraordinary through our church and would like for you to be a part. Please prayerfully consider our church as a place you would like to worship and fellowship with us as we continue to grow.</p>
    <p>As you venture on our website please feel free to contact us through email, phone, or leave a prayer request for us to pray on your behalf. Please take a minute and look at our upcoming events.</p>
    <p class="hope">We hope you will visit us real soon.</p>
  </section>

  <aside class="abs visit">
    <h2>Visit Us</h2>
    <div class="org">Harvest Gateway</div>
    <div>2840 Meadowbrook Ave. Riverside NY 11502</div>
    <div>info@harvestgateway.org</div>
    <div>555.014.2273</div>
    <h4>Service Times</h4>
    <div>Mon - Fri : 7.00 p.m - 8.00 p.m</div>
    <div>Sunday &nbsp;: &nbsp;7.00 a.m - 9.30 a.m</div>
  </aside>

  <section class="abs prayer">
    <h2>View Prayer Listing</h2>
    <div class="search">search</div>
    <div class="req-title">Unspoken request</div>
    <div class="req-row">i feel like giving up please pray for me and other issues i'm going through in my life. <b>Marcus</b></div>
    <div class="req-meta"><span>Viewed <i>(328)</i></span><span>Prayer Requested By : <span style="color:#222">Marcus, 03-28-2012 - 11:08:41 AM</span></span></div>
    <div class="pager">&#x27E8; &#x27E9;</div>
    <div class="sort">sort by <span style="float:right">&#9662;</span></div>
  </section>

  <section class="abs donate">
    <h2>Donate<small>using</small><span class="pay">PayLink</span></h2>
    <p>Excepteur sint occaecat cupidatat non proident, sunt in culpa.</p>
  </section>
  <section class="abs shop">
    <h2>Shop From Us</h2>
    <svg class="cart" width="18" height="16" viewBox="0 0 18 16" fill="none" stroke="#0b4a7a" stroke-width="1.5"><path d="M1 2h3l2 8h9l2-6H5"/><circle cx="7" cy="13.5" r="1.3"/><circle cx="14" cy="13.5" r="1.3"/></svg>
    <p>Excepteur sint occaecat cupidatat non proident, sunt in culpa.</p>
  </section>

  <h2 class="abs cal-title">Event Calendar</h2>
  <div class="abs cal-month">June / 2014 <span>&#x27E8; &#x27E9;</span></div>
  <div class="abs cal">
    <div></div><div></div><div></div><div></div><div></div><div></div><div>1</div>
    <div>2</div><div>3</div><div>4</div><div class="ev">5<small>Prayer meeting</small></div><div>6</div><div>7</div><div>8</div>
    <div>9</div><div>10</div><div>11</div><div>12</div><div>13</div><div class="ev">14<small>Prayer meeting</small></div><div>15</div>
    <div>16</div><div class="ev">17<small>Prayer meeting</small></div><div>18</div><div>19</div><div>20</div><div>21</div><div>22</div>
    <div>23</div><div>24</div><div>25</div><div>26</div><div>27</div><div>28</div><div>29</div>
    <div>30</div><div></div><div></div><div></div><div></div><div></div><div></div>
  </div>

  <p class="abs quote">"No limits, No Boundaries, but increase in Jesus name"</p>

  <nav class="abs nav foot-nav">
    <a>Home</a><a>About Us</a><a>Events</a><a>Prayer Request</a><a>Resources</a><a>Donate</a><a>Contact Us</a>
  </nav>
  <footer class="abs footer">
    <div class="foot-links"><div>Meet Our Staffs</div><div>Group Services</div><div>Resources</div></div>
    <div class="follow">Follow Us &amp; get updated
      <div class="social"><span aria-label="Social network 1"></span><span aria-label="Social network 2"></span><span aria-label="News feed"></span><span aria-label="Social network 3"></span></div>
    </div>
    <div class="legal">Privacy Policy | Terms Conditions | Sitemap | Contact Us<br>&copy; 2014 HGFM. All Rights Reserved</div>
  </footer>
</div>
</body>
</html>
```